Healthcare and Professional IT Services Company need a redesigned business card

We are a IT Services company that targets small medical practices and professional business such as Attorneys, Accounts, Architects etc. We want to communicate a professional yet friendly image using recent logo redesign here on ArtHarbor. Like to see the colors blue and orange in the design. Must use the Tall Pine Computing as displayed in the new logo - then also want to incorporate the fish logo as well.

Target Market(s)

Small medical and professional services

Industry/Entity Type

It Company

Contact Information for Business Card

The usual stuff, place for name address phone website. Also maybe our tagline which is "hooked on technology"

Requirements
Must have
• My new logo and the fish somewhere on the card

```html
<!DOCTYPE html>
<html lang="en">
<head>
<meta charset="utf-8">
<title>Tall Pine Computing – Business Card</title>
<link href="https://fonts.googleapis.com/css2?family=Open+Sans:wght@400;600&display=swap" rel="stylesheet">
<style>
  :root {
    --bg: #e9e6e1;
    --card-white: #ffffff;
    --sky: #6cc6ee;
    --sky-light: #84d0f2;
    --line-blue: #5a7fc4;
    --brand-blue: #4f86c6;
    --accent-orange: #e98a4f;
    --ink: #111111;
  }
  * { box-sizing: border-box; margin: 0; padding: 0; }
  html, body { width: 1200px; height: 892px; overflow: hidden; }
  body {
    background: var(--bg);
    position: relative;
    font-family: "Open Sans", Arial, sans-serif;
    color: var(--ink);
  }
  .card {
    position: absolute;
    width: 560px;
    height: 320px;
    background: var(--card-white);
    box-shadow: 0 6px 18px rgba(0,0,0,0.18);
    overflow: hidden;
  }
  .card-back { left: 600px; top: 70px; }
  .card-front { left: 40px; top: 470px; }

  .brand {
    position: absolute;
    display: flex;
    align-items: center;
    gap: 14px;
  }
  .brand-mark {
    width: 46px; height: 46px;
    border-radius: 50%;
    background: var(--accent-orange);
    flex: none;
  }
  .brand-name {
    font-family: "Open Sans", Arial, sans-serif;
    font-weight: 600;
    font-size: 34px;
    color: var(--brand-blue);
    letter-spacing: 0.5px;
    white-space: nowrap;
  }
  .card-back .brand { left: 50%; top: 50%; transform: translate(-50%, -50%); }

  .front-top-strip { position: absolute; left: 0; top: 0; width: 100%; height: 22px; background: var(--sky-light); }
  .front-logo-band { position: absolute; left: 0; top: 22px; width: 100%; height: 96px; background: var(--card-white); }
  .front-logo-band .brand { left: 50%; top: 50%; transform: translate(-50%, -50%); }
  .front-logo-band .brand-name { font-size: 30px; }
  .front-logo-band .brand-mark { width: 40px; height: 40px; }
  .front-divider-line { position: absolute; left: 0; top: 118px; width: 100%; height: 3px; background: var(--line-blue); }
  .front-info { position: absolute; left: 0; top: 121px; width: 100%; height: 169px; background: var(--sky); }
  .front-bottom-strip { position: absolute; left: 0; top: 290px; width: 100%; height: 30px; background: var(--sky-light); }

  .person-name {
    position: absolute; left: 30px; top: 48px;
    font-size: 27px; font-weight: 400; color: var(--ink);
  }
  .info-rule {
    position: absolute; left: 278px; top: 28px;
    width: 2px; height: 112px; background: var(--ink);
  }
  .contact-list {
    position: absolute; left: 296px; top: 38px;
    list-style: none;
    font-size: 16px; line-height: 30px;
  }
  .contact-list li { display: flex; align-items: center; gap: 10px; white-space: nowrap; }
  .contact-icon {
    width: 16px; height: 16px; background: var(--ink);
    display: flex; align-items: center; justify-content: center; flex: none;
  }
</style>
</head>
<body>

<section class="card card-back" aria-label="Business card back">
  <div class="brand">
    <span class="brand-mark"></span>
    <span class="brand-name">Tall Pine Computing</span>
  </div>
</section>

<section class="card card-front" aria-label="Business card front">
  <div class="front-top-strip"></div>
  <div class="front-logo-band">
    <div class="brand">
      <span class="brand-mark"></span>
      <span class="brand-name">Tall Pine Computing</span>
    </div>
  </div>
  <div class="front-divider-line"></div>
  <div class="front-info">
    <p class="person-name">Marcus Ellwood</p>
    <div class="info-rule"></div>
    <ul class="contact-list">
      <li>
        <span class="contact-icon">
          <svg width="12" height="12" viewBox="0 0 12 12"><path d="M3 1 L5 3 L4 4.5 Q5 7 7.5 8 L9 7 L11 9 L9.5 11 Q3 10 1 2.5 Z" fill="#fff"/></svg>
        </span>+94 5120 8847
      </li>
      <li>
        <span class="contact-icon">
          <svg width="12" height="12" viewBox="0 0 12 12"><circle cx="6" cy="6" r="4.6" fill="none" stroke="#fff" stroke-width="1.2"/><path d="M1.5 6 H10.5 M6 1.5 Q3.5 6 6 10.5 M6 1.5 Q8.5 6 6 10.5" fill="none" stroke="#fff" stroke-width="1"/></svg>
        </span>www.tallpinecomputing.com
      </li>
      <li>
        <span class="contact-icon">
          <svg width="12" height="12" viewBox="0 0 12 12"><path d="M6 11 Q2.5 6.5 2.5 4.5 A3.5 3.5 0 0 1 9.5 4.5 Q9.5 6.5 6 11 Z" fill="#fff"/><circle cx="6" cy="4.5" r="1.3" fill="#111"/></svg>
        </span>4820 Cedar Row, Millbrook, BC
      </li>
    </ul>
  </div>
  <div class="front-bottom-strip"></div>
</section>

</body>
</html>
```